Business Card For Construction Company
Falcon Ridge Contractors
Business Card For Construction Company - Construction
Creative Brief
Professional
Tobias Varnell
No Address
TobiasVarnell@FalconRidgeCorp.example
www.FalconRidgeCorp.example

```html
<!DOCTYPE html>
<html lang="en">
<head>
<meta charset="utf-8">
<title>Falcon Ridge Contractors – Stationery</title>
<link rel="stylesheet" href="https://fonts.googleapis.com/css2?family=Exo+2:wght@800&family=Open+Sans:wght@400;600&display=swap">
<style>
:root{
  --bg:#eceef1;
  --paper:#ffffff;
  --blue:#1f5fae;
  --blue-dark:#173f7a;
  --grey:#6d7278;
  --grey-light:#b9bdc2;
  --ink:#4a4f55;
  --faint:#edf1f6;
}
*{margin:0;padding:0;box-sizing:border-box}
html,body{width:1200px;height:936px;overflow:hidden;background:var(--bg);font-family:"Open Sans",sans-serif;color:var(--ink)}
.canvas{position:relative;width:1200px;height:936px}
.sheet{position:absolute;background:var(--paper);overflow:hidden}
.brand{font-family:"Exo 2",sans-serif;font-weight:800;color:var(--blue);text-transform:uppercase;letter-spacing:.02em;line-height:1.05}
.brand-mark{display:inline-block;background:var(--blue);vertical-align:middle}
.swoosh{position:absolute;left:0;bottom:0;width:100%;display:block}

.letterhead{left:190px;top:76px;width:380px;height:531px}
.letterhead .head-brand{position:absolute;left:20px;top:24px;display:flex;align-items:center;gap:6px}
.letterhead .head-brand .brand-mark{width:14px;height:14px}
.letterhead .head-brand .brand{font-size:9px;width:110px}
.letterhead .contact{position:absolute;left:222px;top:22px;font-size:6px;line-height:9px;color:var(--grey);white-space:nowrap}
.letterhead .contact li{list-style:none;display:flex;align-items:center;gap:4px}
.letterhead .contact li::before{content:"";width:5px;height:5px;background:var(--blue)}
.letterhead .watermark{position:absolute;left:40px;top:140px;width:300px;font-size:34px;color:var(--faint);text-align:center}

.folder{left:633px;top:76px;width:460px;height:536px}
.folder .cover-brand{position:absolute;left:0;right:0;top:200px;text-align:center}
.folder .cover-brand .brand-mark{width:46px;height:46px;margin-bottom:12px}
.folder .cover-brand .brand{font-size:36px;display:block}
.folder .cover-brand .rule{display:block;width:240px;height:3px;background:var(--grey);margin:10px auto 0}

.card{width:194px;height:96px;left:46px}
.card-front{top:663px}
.card-front .card-brand{position:absolute;left:14px;top:12px;display:flex;align-items:center;gap:5px}
.card-front .card-brand .brand-mark{width:12px;height:12px}
.card-front .card-brand .brand{font-size:8px;width:90px}
.card-front .person{position:absolute;left:14px;top:40px;font-size:6px;line-height:9px;white-space:nowrap}
.card-front .person b{display:block;font-weight:600;color:var(--blue-dark)}
.card-front .phones{position:absolute;left:98px;top:40px;font-size:6px;line-height:9px;color:var(--grey);border-left:1px solid var(--grey-light);padding-left:6px;white-space:nowrap}
.card-front .email{position:absolute;left:14px;top:62px;font-size:6px;line-height:9px;color:var(--grey);white-space:nowrap}
.card-back{top:784px}
.card-back .card-brand{position:absolute;left:0;right:0;top:26px;text-align:center}
.card-back .card-brand .brand{font-size:10px}
.card-back .web{position:absolute;left:0;right:0;bottom:10px;text-align:center;font-size:5.5px;color:var(--grey);letter-spacing:.08em}

.envelope-letter{left:266px;top:670px;width:361px;height:208px}
.envelope-letter .env-brand{position:absolute;left:14px;top:16px;display:flex;align-items:center;gap:6px}
.envelope-letter .env-brand .brand-mark{width:14px;height:14px}
.envelope-letter .env-brand .brand{font-size:9px;width:110px}

.envelope-flap{left:663px;top:670px;width:430px;height:208px}
.envelope-flap .flap{position:absolute;left:0;top:0;width:100%;height:46px;display:block}
.envelope-flap .flap-web{position:absolute;left:0;right:0;top:12px;text-align:center;font-size:8px;color:#fff;letter-spacing:.22em;text-transform:uppercase}
</style>
</head>
<body>
<main class="canvas">

  <section class="sheet letterhead" aria-label="Letterhead">
    <div class="head-brand"><span class="brand-mark"></span><span class="brand">Falcon Ridge Contractors</span></div>
    <ul class="contact">
      <li>T 555 014 2200</li>
      <li>F 555 014 2201</li>
      <li>TobiasVarnell@FalconRidgeCorp.example</li>
      <li>www.FalconRidgeCorp.example</li>
    </ul>
    <div class="watermark brand">Falcon Ridge</div>
    <svg class="swoosh" viewBox="0 0 380 80" preserveAspectRatio="none" height="80">
      <path d="M0 40 Q190 0 380 14 L380 22 Q190 8 0 50Z" fill="var(--grey)"/>
      <path d="M0 58 Q200 14 380 30 L380 80 L0 80Z" fill="var(--blue)"/>
    </svg>
  </section>

  <section class="sheet folder" aria-label="Presentation folder">
    <div class="cover-brand">
      <span class="brand-mark"></span>
      <span class="brand">Falcon Ridge<br>Contractors</span>
      <span class="rule"></span>
    </div>
    <svg class="swoosh" viewBox="0 0 460 90" preserveAspectRatio="none" height="90">
      <path d="M0 44 Q230 0 460 16 L460 25 Q230 9 0 55Z" fill="var(--grey)"/>
      <path d="M0 64 Q240 16 460 34 L460 90 L0 90Z" fill="var(--blue)"/>
    </svg>
  </section>

  <section class="sheet card card-front" aria-label="Business card front">
    <div class="card-brand"><span class="brand-mark"></span><span class="brand">Falcon Ridge Contractors</span></div>
    <div class="person"><b>Tobias Varnell</b>President</div>
    <div class="phones">T 555 014 2200<br>C 555 014 2277</div>
    <div class="email">TobiasVarnell@FalconRidgeCorp.example</div>
    <svg class="swoosh" viewBox="0 0 194 18" preserveAspectRatio="none" height="18">
      <path d="M0 12 Q100 0 194 6 L194 18 L0 18Z" fill="var(--blue)"/>
    </svg>
  </section>

  <section class="sheet card card-back" aria-label="Business card back">
    <div class="card-brand"><span class="brand">Falcon Ridge Contractors</span></div>
    <div class="web">www.FalconRidgeCorp.example</div>
  </section>

  <section class="sheet envelope-letter" aria-label="Envelope front">
    <div class="env-brand"><span class="brand-mark"></span><span class="brand">Falcon Ridge Contractors</span></div>
  </section>

  <section class="sheet envelope-flap" aria-label="Envelope back">
    <svg class="flap" viewBox="0 0 430 46" preserveAspectRatio="none">
      <path d="M0 0 H430 V38 Q215 30 0 42Z" fill="var(--blue)"/>
    </svg>
    <div class="flap-web">www.FalconRidgeCorp.example</div>
  </section>

</main>
</body>
</html>
```